Summit Bodyform Gym Website

We need a website design for our gym.

Summit is the UAE's first calisthenics and parkour gym. The theme under which the gym revolves is that one does not require any machinery to workout as our bodies could be themselves the machinery. The gym is designed to be the more of a social hub rather than an "in-and-out" gym, where people come train, have fun, hang out and socialize for a few hours rather than just train for 60 minutes then leave. The gym is designed to be a big open space with lots of natural sunlight, natural wood and plants all over the place to create a natural and refreshing setting. We also use recycled material throughout the gym and recycle our waste as being green is part of our philosophy. We currently also have some of the world's top and most recognized calisthenics athletes working with us.

We would like our website to reflect all that as well as provide a simple, interactive and fun way for visitors to be able to get class and gym information, check out gym media and contact us for bookings.

Target Market(s)

Ages 15-35

Industry/Entity Type

Fitness

Coding

Coded - Design and coding required

Number of Pages Required

4 page

Font styles to use
Decorative

Colors
0792cd

Requirements
Must have
• Class descriptions
• Gym description
• Class schedules
• Trainer profiles
• Gym philosophy
• Contact Details
Nice to have
• A link to contact us directly for a free first trial class

```html
<!DOCTYPE html>
<html lang="en">
<head>
<meta charset="utf-8">
<title>Summit Bodyform Gym</title>
<link href="https://fonts.googleapis.com/css2?family=Montserrat:wght@400;600;700&family=Open+Sans:ital,wght@0,400;0,600;0,700;1,400&display=swap" rel="stylesheet">
<style>
:root{
  --blue:#0792cd;
  --blue-light:#0aa3d4;
  --dark:#222222;
  --darker:#1c1c1c;
  --ink:#111111;
  --body:#444444;
  --muted:#8a8a8a;
  --grey-bg:#e9e9e9;
  --white:#ffffff;
  --line:#333333;
}
*{box-sizing:border-box;margin:0;padding:0}
html,body{width:1200px;height:2521px;overflow:hidden}
body{font-family:'Open Sans',sans-serif;color:var(--body);background:var(--white);position:relative}

/* top bar */
.topbar{height:37px;background:var(--dark);display:flex;align-items:center;justify-content:space-between;padding:0 99px 0 101px;font-family:'Montserrat',sans-serif;font-size:10px;color:#9a9a9a;letter-spacing:.3px}
.topbar b{color:#e0e0e0;font-weight:600}
.social-top{display:flex;height:37px}
.social-top span{width:38px;height:37px;border-left:1px solid #333;display:flex;align-items:center;justify-content:center}
.social-top span:last-child{border-right:1px solid #333}
.social-top i{width:11px;height:11px;background:#777;display:block;border-radius:2px}

/* header */
.header{height:114px;display:flex;align-items:center;padding:0 99px 0 92px;justify-content:space-between}
.brand{display:flex;align-items:center;gap:10px;font-family:'Montserrat',sans-serif;font-weight:700;font-size:32px;color:var(--ink)}
.brand .dot{width:16px;height:16px;border-radius:50%;background:var(--blue)}
.nav{display:flex;gap:4px;align-items:center}
.nav a{font-family:'Montserrat',sans-serif;font-size:11px;color:#222;text-decoration:none;text-transform:uppercase;padding:12px 9px;letter-spacing:.2px}
.nav a.active{border:2px solid var(--blue);color:var(--blue);padding:10px 13px}

/* hero */
.hero{height:563px;position:relative;background:linear-gradient(120deg,#5b6f80 0%,#3a6fa3 30%,#8b93a0 55%,#4b5560 80%,#2f3438 100%)}
.hero .photo{position:absolute;inset:0}
.hero-arrow{position:absolute;top:252px;width:54px;height:54px;display:flex;align-items:center;justify-content:center}
.hero-arrow.prev{left:30px;border:1px solid rgba(255,255,255,.35)}
.hero-arrow.next{left:1112px;background:#1e1e1e;border:1px solid #666}
.hero-text{position:absolute;left:108px;top:338px}
.hero-line{display:inline-block;background:rgba(40,40,40,.82);color:#fff;font-family:'Montserrat',sans-serif;font-size:16px;text-transform:uppercase;padding:10px 16px;letter-spacing:.4px;line-height:22px}
.hero-btn{display:inline-block;margin-top:20px;background:var(--blue);color:#fff;font-family:'Montserrat',sans-serif;font-size:16px;text-transform:uppercase;padding:13px 18px;letter-spacing:.4px}

/* trial band */
.trial{height:128px;background:var(--blue-light);display:flex;align-items:center;justify-content:center;gap:40px}
.trial p{font-family:'Montserrat',sans-serif;font-size:25px;color:#fff}
.trial a{border:2px solid #fff;color:#fff;font-family:'Montserrat',sans-serif;font-size:16px;text-transform:uppercase;padding:14px 36px;text-decoration:none}

/* main grey area */
.main{height:1149px;background:var(--grey-bg);padding:69px 99px 0 99px}
.row{display:flex;gap:8px}
.side{width:153px;padding:22px 25px;color:#fff}
.side h3{font-family:'Montserrat',sans-serif;font-size:19px;text-transform:uppercase;font-weight:400;line-height:22px;letter-spacing:.5px;color:#fff}
.side p{font-size:10px;line-height:15px;margin-top:18px}
.side .ctrl{display:flex;gap:10px;margin-top:22px}
.side .ctrl span{width:32px;height:28px;border:1px solid #666;display:flex;align-items:center;justify-content:center}
.classes .side{background:var(--darker)}
.classes .side p{color:#bbb}
.card{width:276px;height:413px;background:var(--white);text-align:center}
.card .img{height:215px;position:relative}
.card .time{position:absolute;left:50%;bottom:0;transform:translateX(-50%);background:var(--blue);color:#fff;font-family:'Montserrat',sans-serif;font-size:11px;padding:12px 26px;white-space:nowrap}
.card h4{font-family:'Montserrat',sans-serif;font-size:15px;margin-top:26px;text-transform:uppercase;color:var(--ink);font-weight:600}
.rule{width:46px;height:1px;background:#222;margin:12px auto 18px}
.card p{font-size:11px;line-height:16px;color:#333;padding:0 26px}
.btn-outline{display:inline-block;border:1px solid #222;font-family:'Montserrat',sans-serif;font-size:10px;text-transform:uppercase;padding:9px 26px;color:#222;margin-top:16px}

.trainers{margin-top:41px;height:223px}
.trainers .side{background:var(--blue-light)}
.trainers .side p{color:#fff}
.trainers .side .ctrl span{border-color:#fff}
.trainers .side .ctrl span.on{background:#fff}
.trainer-img{width:276px;height:223px}
.trainer-info{flex:1;background:var(--white);padding:22px 30px}
.trainer-info h4{font-family:'Montserrat',sans-serif;font-size:15px;font-weight:600;color:var(--ink)}
.trainer-info p{font-size:11.5px;line-height:17px;color:#333;margin-top:14px;max-width:520px}
.trainer-info .btn-outline{margin-top:30px}

.testimonials{margin-top:45px;background:var(--white);height:254px;text-align:center;padding-top:32px;position:relative}
.testimonials h4{font-family:'Montserrat',sans-serif;font-size:15px;font-weight:600;color:var(--ink)}
.testimonials .rule{margin:10px auto 22px}
.quote{font-style:italic;font-size:12px;line-height:20px;color:#555;width:850px;margin:0 auto}
.qmark{position:absolute;font-family:Georgia,serif;font-size:48px;color:#bbb}
.author{font-size:10px;margin-top:16px;color:#444}
.author b{color:#111}
.dots{display:flex;justify-content:center;gap:8px;margin-top:22px}
.dots span{width:9px;height:9px;background:#c2c8cc}
.dots span.on{background:var(--blue)}

/* footer */
.footer{height:530px;background:var(--dark);position:relative}
.strip{position:absolute;left:99px;top:0;width:1002px;height:85px;display:flex}
.strip-item{flex:1;background:linear-gradient(90deg,#0788bf,#0aa3d4);display:flex;align-items:center;padding-left:40px;gap:22px;color:#fff}
.strip-text{display:block}
.strip-text h5{font-family:'Montserrat',sans-serif;font-size:15px;font-weight:400;letter-spacing:1px;text-transform:uppercase;white-space:nowrap}
.strip-text p{font-family:'Montserrat',sans-serif;font-size:12px;margin-top:4px;white-space:nowrap}
.cols{position:absolute;top:152px;left:97px;right:97px;display:flex}
.col h5{font-family:'Montserrat',sans-serif;font-size:15px;color:#fff;text-transform:uppercase;font-weight:600}
.col .rule{margin:10px 0 20px;background:#fff;width:40px}
.posts{width:404px}
.post{border-bottom:1px solid var(--line);padding-bottom:18px;margin-bottom:18px;width:320px}
.post h6{font-size:11px;color:#ddd;font-weight:400}
.post p{font-size:11px;color:#666;line-height:16px;margin-top:8px}
.post small{display:block;font-size:9.5px;color:#bbb;margin-top:10px}
.hours{width:402px}
.hours li{list-style:none;display:flex;justify-content:space-between;font-size:11px;color:#6f6f6f;border-bottom:1px solid var(--line);padding:12px 0;width:322px}
.hours li span:first-child{display:flex;align-items:center;gap:10px}
.hours li span:first-child::before{content:"";width:8px;height:8px;border:2px solid var(--blue);border-radius:50%}
.contact{width:220px}
.contact li{list-style:none;display:flex;gap:14px;font-size:11px;color:#bbb;margin-bottom:26px;line-height:18px}
.social-foot{display:flex;gap:20px;margin-top:4px}
.social-foot i{width:14px;height:14px;background:#888;display:block;border-radius:2px}
.copyright{position:absolute;top:487px;width:100%;text-align:center;font-size:11px;color:#ddd}
</style>
</head>
<body>

<div class="topbar">
  <div>OPENING HOURS : MON - SAT <b>6AM - 9PM</b>, SUN <b>8AM - 6PM</b></div>
  <div class="social-top" aria-label="Social links">
    <span><i></i></span><span><i></i></span><span><i></i></span><span><i></i></span><span><i></i></span><span><i></i></span><span><i></i></span><span><i></i></span><span><i></i></span>
  </div>
</div>

<header class="header">
  <div class="brand"><span class="dot"></span>Summit</div>
  <nav class="nav">
    <a class="active">Home</a>
    <a>Class Descriptions</a>
    <a>Gym Description</a>
    <a>Class Schedules</a>
    <a>Trainer Profiles</a>
    <a>Gym Philosophy</a>
    <a>Contact</a>
  </nav>
</header>

<section class="hero">
  <div class="photo" role="img" aria-label="Wooden gymnastics ring hanging in a blue-framed training gym"></div>
  <div class="hero-arrow prev"><svg width="10" height="14" viewBox="0 0 10 14"><path d="M7 2 2 7l5 5" stroke="#fff" stroke-width="1.5" fill="none"/></svg></div>
  <div class="hero-arrow next"><svg width="10" height="14" viewBox="0 0 10 14"><path d="M3 2l5 5-5 5" stroke="#fff" stroke-width="1.5" fill="none"/></svg></div>
  <div class="hero-text">
    <span class="hero-line">The theme under which the gym revolves is that one does</span><br>
    <span class="hero-line">not require any machinery to workout as our bodies</span><br>
    <span class="hero-line">could be themselves the machinery</span><br>
    <span class="hero-btn">Request for quote</span>
  </div>
</section>

<section class="trial">
  <p>Lorem ipsum dolor sit amet consectetur</p>
  <a>Free first trial class</a>
</section>

<main class="main">
  <div class="row classes">
    <div class="side">
      <h3>Popular<br>Classes</h3>
      <p>Sed lacinia non urna eget mattis. Vestibu-lum eget</p>
      <div class="ctrl">
        <span><svg width="6" height="9" viewBox="0 0 6 9"><path d="M5 1 1 4.5 5 8" stroke="#fff" fill="none"/></svg></span>
        <span><svg width="6" height="9" viewBox="0 0 6 9"><path d="M1 1l4 3.5L1 8" stroke="#fff" fill="none"/></svg></span>
      </div>
    </div>
    <article class="card">
      <div class="img" role="img" aria-label="Woman on a spin bike in a cycling class" style="background:linear-gradient(135deg,#e9c27a,#d86b9a 55%,#7a3b6a)"><span class="time">4 PM - 6 PM</span></div>
      <h4>Lorem ipsum</h4><div class="rule"></div>
      <p>Lorem ipsum dolor sit amet, consectetur adipiscing elit. Proin luctus aliquam lectus non posuere.</p>
      <span class="btn-outline">Read more</span>
    </article>
    <article class="card">
      <div class="img" role="img" aria-label="Group aerobics class in a bright studio" style="background:linear-gradient(135deg,#9fc3d8,#e3a2a8 55%,#6b8fa8)"><span class="time">2 PM - 4 PM</span></div>
      <h4>Contantry popilar</h4><div class="rule"></div>
      <p>Lorem ipsum dolor sit amet, consectetur adipiscing elit. Proin luctus aliquam lectus non posuere. Donec diam ligula, volutpat sit amet</p>
    </article>
    <article class="card">
      <div class="img" role="img" aria-label="Step aerobics class in a studio with large windows" style="background:linear-gradient(135deg,#cfd6dc,#b48b8a 55%,#5e5f66)"><span class="time">6 PM - 8 PM</span></div>
      <h4>Popilar sit</h4><div class="rule"></div>
      <p>Lorem ipsum dolor sit amet, consectetur adipiscing elit. Proin luctus aliquam lectus non posuere. Donec diam ligula, volutpat sit amet</p>
    </article>
  </div>

  <div class="row trainers">
    <div class="side">
      <h3>Our<br>Trainners</h3>
      <p>Sed lacinia non urna eget mattis. Vestibu-lum eget</p>
      <div class="ctrl">
        <span><svg width="6" height="9" viewBox="0 0 6 9"><path d="M5 1 1 4.5 5 8" stroke="#fff" fill="none"/></svg></span>
        <span class="on"><svg width="6" height="9" viewBox="0 0 6 9"><path d="M1 1l4 3.5L1 8" stroke="#222" fill="none"/></svg></span>
      </div>
    </div>
    <div class="trainer-img" role="img" aria-label="Trainer seated on a weight bench in a dark gym" style="background:linear-gradient(135deg,#1a1a1a,#4a4a4a 50%,#2a2a2a)"></div>
    <div class="trainer-info">
      <h4>JHONE DOE</h4>
      <p>Sed lacinia non urna eget mattis. Vestibulum eget lorem ac turpis malesuada porttitor. Morbi dignissim magna dolor, varius consequat dolor vulputate ac. Vestibulum ante ipsum primis in faucibus orci luctus et ultrices posuere cubilia Curae; Proin nec purus ante. Proin ac mi elementum.</p>
      <span class="btn-outline">Read more</span>
    </div>
  </div>

  <section class="testimonials">
    <h4>TESTIMONIALS</h4><div class="rule"></div>
    <span class="qmark" style="left:48px;top:60px">&ldquo;</span>
    <span class="qmark" style="right:48px;top:96px">&rdquo;</span>
    <p class="quote">In ut urna a augue iaculis sagittis. Aliquam vitae turpis eros. Nam congue mauris vel metus pellentesque, semper condimentum neque fringilla. Curabitur ultrices tincidunt nibh, non lobortis mi semper sit amet. Nunc vehicula sollicitudin imperdiet. Vestibulum at nisi lobortis magna dictum aliquam in et elit. Curabitur urna diam, lobortis sed tellus nec</p>
    <p class="author"><b>Marten,</b> Lorem ipsum</p>
    <div class="dots"><span class="on"></span><span></span><span></span><span></span></div>
  </section>
</main>

<footer class="footer">
  <div class="strip">
    <div class="strip-item">
      <svg width="20" height="20" viewBox="0 0 24 24"><path d="M6.6 10.8a15 15 0 0 0 6.6 6.6l2.2-2.2c.3-.3.7-.4 1-.2 1.1.4 2.3.6 3.6.6.6 0 1 .4 1 1V20c0 .6-.4 1-1 1A17 17 0 0 1 3 4c0-.6.4-1 1-1h3.5c.6 0 1 .4 1 1 0 1.3.2 2.5.6 3.6.1.3 0 .7-.2 1z" fill="#fff"/></svg>
      <div class="strip-text"><h5>Quick contact</h5><p>Call Us On +4410258</p></div>
    </div>
    <div class="strip-item">
      <svg width="20" height="20" viewBox="0 0 20 20"><rect x="2" y="4" width="16" height="14" fill="none" stroke="#fff" stroke-width="2"/><path d="M2 8h16M6 2v4M14 2v4" stroke="#fff" stroke-width="2"/><path d="M5 11h2v2H5zm4 0h2v2H9zm4 0h2v2h-2zm-8 3h2v2H5zm4 0h2v2H9z" fill="#fff"/></svg>
      <div class="strip-text"><h5>Events</h5><p>Jan 2016- Lorem ipsum dolor</p></div>
    </div>
    <div class="strip-item">
      <svg width="22" height="16" viewBox="0 0 22 16"><rect width="22" height="16" rx="1" fill="#fff"/><path d="M1 1l10 8 10-8" stroke="#0a9cc9" stroke-width="1.5" fill="none"/></svg>
      <div class="strip-text"><h5>Contact info</h5><p>Lorem ipsum dolor sit amet, consec</p></div>
    </div>
  </div>

  <div class="cols">
    <div class="col posts">
      <h5>Recent posts</h5><div class="rule"></div>
      <div class="post">
        <h6>The do's and don'ts of running for fitness</h6>
        <p>Sed rhoncus nulla turpis, vitae rutrum velit iaculis et. Curabitur vestibulum, erat non im</p>
        <small>June 2, 2015, by Lorem ipsum</small>
      </div>
      <div class="post" style="border:none">
        <h6>Get six-pack abs like the pros on the bars</h6>
        <p>Sed rhoncus nulla turpis, vitae rutrum velit iaculis et. Curabitur vestibulum, erat non im</p>
        <small>June 2, 2015, by Lorem ipsum</small>
      </div>
    </div>
    <div class="col hours">
      <h5>Opening hours</h5><div class="rule"></div>
      <ul>
        <li><span>Monday</span><span>8.00 AM - 4.00 PM</span></li>
        <li><span>Wednesday</span><span>8.00 AM - 4.00 PM</span></li>
        <li><span>Friday</span><span>8.00 AM - 4.00 PM</span></li>
        <li><span>Saturday</span><span>9.00 AM - 5.00 PM</span></li>
        <li style="border:none"><span>Sunday</span><span>closed</span></li>
      </ul>
    </div>
    <div class="col contact">
      <h5>Contact info</h5><div class="rule"></div>
      <ul>
        <li><svg width="12" height="10" viewBox="0 0 12 10"><rect x=".5" y=".5" width="11" height="9" fill="none" stroke="#ccc"/><path d="M1 1l5 4 5-4" stroke="#ccc" fill="none"/></svg>hello@summitbodyform.com</li>
        <li><svg width="12" height="12" viewBox="0 0 24 24"><path d="M6.6 10.8a15 15 0 0 0 6.6 6.6l2.2-2.2c.3-.3.7-.4 1-.2 1.1.4 2.3.6 3.6.6.6 0 1 .4 1 1V20c0 .6-.4 1-1 1A17 17 0 0 1 3 4c0-.6.4-1 1-1h3.5c.6 0 1 .4 1 1 0 1.3.2 2.5.6 3.6.1.3 0 .7-.2 1z" fill="#ccc"/></svg>Tel. 48 20 17 309</li>
        <li><svg width="10" height="14" viewBox="0 0 10 14"><path d="M5 0a5 5 0 0 0-5 5c0 4 5 9 5 9s5-5 5-9a5 5 0 0 0-5-5zm0 7a2 2 0 1 1 0-4 2 2 0 0 1 0 4z" fill="#ccc"/></svg><span>lorem ipsum dolor<br>Granvej 24 4100 Halden</span></li>
      </ul>
      <div class="social-foot"><i></i><i></i><i></i><i></i><i></i><i></i></div>
    </div>
  </div>

  <p class="copyright">Copyrights 2015 © All Rights Reserved</p>
</footer>

</body>
</html>
```